SaaS / Consulting / Solution website redesign

We need a website design that:
- Is completely different than our current design : https://plumvessel.net
- Has a very minimal amount of copy
- Changes our positioning from a SaaS application to a solutions company. Solutions company means that we help our customers solve their problems with consulting, training, and tools. An example of a solutions company is here: https://oldpages.example/web/20130111103320/http://www.brindlework.com:80/
- Does not make us look like a start up
- Is more people oriented than technology oriented

We need a designer that:
- Is a rebel at heart
- Is a minimalist
- Tells us why our current site sucks
- Can disagree with us
- Can also do copywriting or already has a copywriter that can help
- Is ok with saying we have capability that we don't in order to see if people actually want that
- Can understand the difference between our grand vision and where we need to focus ourselves today in order to get there

Who we are:
- Entrepreneurs
- Programmers
- Consultants
- Investors

Here's our design goals:
#1 Get customers, investors, employers, and partners excited about our unique and clearly articulated value proposition
#2 Get people to contact us asking for help with their programs
#3 Position ourselves as an expert in the skills based volunteering, mentorship, and group collaboration
#4 Make it easy for people, who already know who we are, to register online

What our grand vision is:
- Create a marketplace where any person can go to our site and find time with anyone they need to meet with. Whether that is their hair stylist, school advisor, parent of your kids class, dentist, attorney, etc.

What will you get if you win:
- In addition to the prize of this project we will have many landing pages and other revisions we will need in the future. We currently don't have a designer or copywriter and need to add that capability to our team

Who do we need to appeal to:
- Directors that are launching innovative programs inside organizations
- IT personnel who are trying to disqualify our technology so they don't have to support it or deal with it when it doesn't go well
- Enterprise IT architects who don't want our product being on its own island within their organization totally incompatible with everything else. Architects which are trying to assess how our platform will co-exist with all their other platforms
- Vice Presidents who want to help their directors understand that we don't have enough experience to help them
- Program managers who have to juggle a million things and need a tool that actually helps instead of confuses them and adds more work for them.
- Program managers & directors that have been given ambiguous goals by their board of directors like "improve retention, increase engagement, create innovation, get people to collaborate." And who have no idea where to start or how to deliver on things like that.
- Program managers, directors, and vice presidents that are trying to understand how our technology and services fit into their existing technology and capability
- Employees who are bored and uninspired with their current tools and are hoping for some excitement in their life. Kind of like candy or a double espresso.
- Investors who think, our company like all the rest, are going to waste their money and make them look like a fool

Other information:
-The CSS and html needs to be responsive

-Our registration onboarding flow needs to collect this information:
User first name
user last name
user email
(verify their email)
user phone number
(verify their phone number)
User profile image (optional)
User profile summary (optional, like a bio, freeform text fiels)
If applicable: Register their organization
Organization name
Organization image (optional)
Account Mailing address
account Billing address (could be same as mailing address)
account Billing email address (could be same as user address)
account Product selection (pricing tier)
account Credit card information

The designs I am getting are a good start but they are only the front page. I just want you to know that I am expecting and need more than a landing page to complete the design. I will likely need a page that outlines the benefits and features of the product itself, how its different than our competitors, which will not be on the front page. I will need a registration flow. I will need a blog page design so we can post blog articles, I will need a team page, a page that goes into detail on our training, our services. I will likely need a page that shows all news and media we have been in. I need to show customer and user quotes, case studies, a way to contact us, partners, general resources like on collaboration, product tutorials, customers. I need the site to address a comprehensive set of needs. I need that design to be consistent and thorough. I know what PlateHarbor is. I'm not using because I need more than a template that was customized. I need to be unique and match our brand thoughtfully, beautifully, and artistically. Someone asked me a question about how Murmly is similar to our tool in the way it is referred by end users and purchased by managers. Our website needs to primarily talk to the managers as I explained in the brief but it needs to appear cool and exciting to our end-users without focusing on the technology too much. Murmly is a tool that teams use to collaborate in small and large enterprises. The value prop for them is that communication is easier. But they don't put that on their website. Why? Because the users of the technology won't go to the website to find out information on it, they get their information from someone who is using it and demos it to them. When Ines tells her manager Otto "Lets get murmly, Ruth is using it at her company and its great" Ines's manager doesn't know anything about murmly so she promptly googles it. The most important thing from Ines's perspective is that Otto agrees to try it out. Otto's biggest concern is that productivity will be enhanced to degraded. Murmly knows this and so on the front page they know they are talking to Otto NOT Ines because Ines is already sold on it and doesn't need to get sold on the website. Ines is end user. Otto is the purchaser. We have the same problem and so our end users are not the ones purchasing our product, their managers are purchasing our product. We get referred by our end users and vetted by their managers. Hope this helps! Thank you for looking at this project!  Added Wednesday, June 7, 2017

Another observation I am having about the designs being submitted. I believe we used the animations on our current website because animations / cartoons connect with the "inner child" in our users. Whatever that means :-). I think it's what makes our brand fun. I have a hard time imagining that we could make the design fun looking without animations but I'm sure it can be achieved. I also recognize that blending pictures of real people and animations is hard. So either we must masterfully blend them, use only animations, or make the real people have a LOT of fun! So far most of the designs while achieve the goal of appealing to the serious Vice Presidents and directors, they are not doing a good job at appealing to the overworked program managers and bored employees. There seems to stand another challenge with animations which is animations are hard to find and/or create that achieve the message / emotion we are trying to communicate. I don't have any good answers for this but I will say we can hire both animators and illustrators if we need to. All you have to do is communicate the effect in the website design with some simpler version maybe not the end illustration or animation itself. Added Wednesday, June 7, 2017

• Sex appeal and a sense of humor. Copy that makes people excited and clairvoyant about our potential.
• Boring renditions of other non-inspiring websites

```html
<!DOCTYPE html>
<html lang="en">
<head>
<meta charset="utf-8">
<title>Plumvessel — Solutions for people who meet in person</title>
<link href="https://fonts.googleapis.com/css2?family=Open+Sans:wght@400;600;700&display=swap" rel="stylesheet">
<style>
:root{
  --blue:#1e8fd8;
  --blue-dark:#1672b0;
  --ink:#2f3338;
  --muted:#6b7077;
  --rule:#d9dde1;
  --tile-dark:#3d4046;
  --tile-light:#e4e5e7;
  --menu-active:#2b3a4e;
  --footer:#ececec;
  --bar:#dedede;
  --white:#ffffff;
}
*{box-sizing:border-box;margin:0;padding:0}
html,body{width:687px;height:1200px;overflow:hidden}
body{font-family:"Open Sans",Arial,sans-serif;color:var(--ink);background:var(--white);position:relative}
ul{list-style:none}

/* hero */
.hero{position:relative;height:205px;overflow:hidden}
.hero-photo{position:absolute;inset:0;background:linear-gradient(100deg,#2a3f55 0%,#4b6a86 45%,#8fa9bd 75%,#5d7891 100%)}
.hero-shade{position:absolute;inset:0;background:linear-gradient(90deg,rgba(20,35,55,.55),rgba(20,35,55,.1))}
.site-nav{position:absolute;top:0;left:0;right:0;height:30px;display:flex;align-items:center;justify-content:space-between;padding:0 18px;z-index:2}
.brand{font-size:19px;font-weight:600;color:var(--blue)}
.menu{display:flex;gap:2px}
.menu a{color:var(--white);text-decoration:none;font-size:9.5px;padding:8px 9px}
.menu a.active{background:var(--blue)}
.hero-copy{position:absolute;left:30px;top:72px;width:320px;z-index:2}
.hero-copy p{color:var(--white);font-size:15px;line-height:1.3}
.btn{display:inline-block;background:var(--blue);color:var(--white);font-size:8.5px;font-weight:700;letter-spacing:.4px;padding:5px 11px;text-decoration:none}
.hero-copy .btn{margin-top:10px}

/* vision */
.vision{text-align:center;padding-top:14px}
.section-title{color:var(--blue);font-weight:400;font-size:23px;line-height:1.2}
.vision h3{font-size:13px;font-weight:600;margin-top:4px}
.vision .lede{font-size:7px;line-height:1.55;color:var(--muted);width:560px;margin:8px auto 0}
.vision .btn{margin-top:10px}
.pillars{display:flex;gap:14px;justify-content:center;margin-top:16px}
.pillar{width:150px;height:88px;border:1px solid var(--rule);border-top:2px solid var(--blue);padding:8px 10px;text-align:center;position:relative;background:var(--white)}
.pillar h4{font-size:8px;color:var(--blue);font-weight:700}
.pillar p{font-size:7px;color:var(--muted);line-height:1.45;margin-top:5px}
.pillar .dot{position:absolute;bottom:8px;left:50%;margin-left:-4px;width:8px;height:8px}

/* who */
.who{text-align:center;margin-top:26px}
.who .section-title{font-size:25px}
.tiles{display:flex;gap:8px;justify-content:center;margin-top:16px}
.tile{width:137px;height:128px;display:flex;flex-direction:column}
.tile-art{flex:1;display:flex;align-items:center;justify-content:center}
.tile-art span{width:64px;height:52px;border-radius:6px;display:block}
.tile.light .tile-art{background:var(--tile-light)}
.tile.light .tile-art span{background:#c9cbcf}
.tile.dark .tile-art{background:var(--tile-dark)}
.tile.dark .tile-art span{background:#5a5e66}
.tile-label{height:30px;line-height:28px;font-size:10px;font-weight:600;background:var(--white);border:1px solid var(--rule);border-top:2px solid var(--blue)}

/* business case */
.business{text-align:center;margin-top:26px}
.cases{display:flex;width:503px;margin:16px auto 0;border:1px solid var(--rule);text-align:left;height:150px}
.case-menu{width:126px;border-right:1px solid var(--rule)}
.case-menu li{font-size:8.5px;padding:6px 10px;border-bottom:1px solid #eceef0;color:var(--ink)}
.case-menu li.active{background:var(--menu-active);color:var(--white)}
.case-body{flex:1;padding:12px 14px}
.case-body h4{font-size:10.5px;font-weight:700;padding-bottom:6px;border-bottom:1px solid var(--rule)}
.case-body li{font-size:8.5px;color:var(--muted);margin-top:6px;padding-left:12px;position:relative}
.case-body li::before{content:"";position:absolute;left:2px;top:4px;width:4px;height:4px;background:var(--blue);border-radius:50%}
.case-photo{width:170px;margin:8px;background:linear-gradient(160deg,#d9e6f1 0%,#8fb1cc 40%,#48739a 75%,#2d4f70 100%)}

/* footer */
.site-footer{position:absolute;left:0;right:0;top:905px;height:265px;background:var(--footer);padding:22px 40px 0}
.footer-cols{display:flex;gap:22px}
.footer-cols h5{font-size:13px;font-weight:400;color:var(--ink);margin-bottom:10px}
.col-links{width:110px}
.col-links li{font-size:8px;color:var(--muted);padding:3px 0 3px 10px;position:relative}
.col-links li::before{content:"›";position:absolute;left:0;top:1px;color:var(--blue)}
.col-quote{width:160px}
.quote{background:var(--white);border:1px solid var(--rule);font-size:7.5px;line-height:1.5;color:var(--muted);padding:8px 10px;font-style:italic}
.quote-by{display:flex;align-items:center;gap:7px;margin-top:10px}
.avatar{width:26px;height:26px;border-radius:50%;background:#b8bec5}
.quote-by strong{display:block;font-size:8px;color:var(--ink)}
.quote-by span{font-size:7px;color:var(--muted)}
.col-contact{width:150px}
.col-contact li{display:flex;gap:7px;font-size:7.5px;color:var(--muted);line-height:1.4;margin-bottom:8px}
.col-contact svg{flex:none;margin-top:1px}
.col-social li{display:flex;align-items:center;gap:7px;font-size:8px;color:var(--ink);margin-bottom:8px}
.col-social li span{width:16px;height:16px;background:var(--blue-dark);display:block}
.copyright{position:absolute;left:0;right:0;bottom:0;height:30px;line-height:30px;text-align:center;font-size:8px;color:var(--muted);background:var(--bar)}
</style>
</head>
<body>

<header class="hero">
  <div class="hero-photo" role="img" aria-label="Photo of a businessman standing at an office window looking out over a city"></div>
  <div class="hero-shade"></div>
  <nav class="site-nav">
    <div class="brand">Plumvessel</div>
    <div class="menu">
      <a class="active" href="#">Home</a><a href="#">About</a><a href="#">Services</a><a href="#">Solutions</a><a href="#">Testimonials</a><a href="#">Contact Us</a>
    </div>
  </nav>
  <div class="hero-copy">
    <p>We are a SaaS company we help our customers to solve their problems with consulting,training, and tools.</p>
    <a class="btn" href="#">LEARN MORE</a>
  </div>
</header>

<section class="vision">
  <h2 class="section-title">The Plumvessel Vision</h2>
  <h3>How we're going to change the world by connecting people in-person</h3>
  <p class="lede">Plumvessel helps people meet face to face with the right person at the right time. We pair smart scheduling with hands-on consulting and training, so programs run smoothly and every meeting counts. From mentoring circles to volunteer days, we make real connections simple to plan, easy to join, and worth showing up for.</p>
  <a class="btn" href="#">READ MORE</a>
  <div class="pillars">
    <div class="pillar">
      <h4>WHAT</h4>
      <p>We're building software that connects people in person</p>
      <svg class="dot" viewBox="0 0 8 8"><circle cx="4" cy="4" r="3.5" fill="none" stroke="#9aa0a6"/></svg>
    </div>
    <div class="pillar">
      <h4>HOW</h4>
      <p>We pair tools with coaching to bring people together</p>
      <svg class="dot" viewBox="0 0 8 8"><circle cx="4" cy="4" r="3.5" fill="none" stroke="#9aa0a6"/></svg>
    </div>
    <div class="pillar">
      <h4>WHY</h4>
      <p>People feel more isolated than ever despite all our technology</p>
      <svg class="dot" viewBox="0 0 8 8"><circle cx="4" cy="4" r="3.5" fill="none" stroke="#9aa0a6"/></svg>
    </div>
  </div>
</section>

<section class="who">
  <h2 class="section-title">Who We are ?</h2>
  <div class="tiles">
    <div class="tile light"><div class="tile-art"><span role="img" aria-label="Icon of an entrepreneur"></span></div><div class="tile-label">Entrepreneurs</div></div>
    <div class="tile dark"><div class="tile-art"><span role="img" aria-label="Icon of a programmer at a computer"></span></div><div class="tile-label">Programmers</div></div>
    <div class="tile dark"><div class="tile-art"><span role="img" aria-label="Icon of a group of consultants"></span></div><div class="tile-label">Consultants</div></div>
    <div class="tile light"><div class="tile-art"><span role="img" aria-label="Icon of an investor"></span></div><div class="tile-label">Investors</div></div>
  </div>
</section>

<section class="business">
  <h2 class="section-title">Business Case</h2>
  <div class="cases">
    <ul class="case-menu">
      <li class="active">Volunteer coordination</li>
      <li>Office hours</li>
      <li>Mentor programs</li>
      <li>Post-event networking</li>
      <li>Professional services</li>
      <li>Traveling networking</li>
    </ul>
    <div class="case-body">
      <h4>Volunteer coordination</h4>
      <ul>
        <li>HR/Enterprise</li>
        <li>Local Government</li>
        <li>Churches</li>
        <li>University</li>
        <li>Non profits</li>
      </ul>
    </div>
    <div class="case-photo" role="img" aria-label="Photo of glass office towers seen from below against a blue sky"></div>
  </div>
</section>

<footer class="site-footer">
  <div class="footer-cols">
    <div class="col-links">
      <h5>Quick Links</h5>
      <ul><li>Home</li><li>About</li><li>Services</li><li>Solutions</li><li>Testimonials</li><li>Contact Us</li></ul>
    </div>
    <div class="col-quote">
      <h5>Testimonials</h5>
      <p class="quote">Working with this team changed how our volunteers meet. Scheduling is simple and our people actually show up.</p>
      <div class="quote-by"><div class="avatar" role="img" aria-label="Portrait of the client quoted"></div><div><strong>Dale Harlow</strong><span>Program Director</span></div></div>
    </div>
    <div class="col-contact">
      <h5>Contact Us</h5>
      <ul>
        <li><svg width="9" height="11" viewBox="0 0 9 11"><path d="M4.5 0.5a3.5 3.5 0 0 1 3.5 3.5c0 2.6-3.5 6.5-3.5 6.5S1 6.6 1 4a3.5 3.5 0 0 1 3.5-3.5z" fill="#1672b0"/><circle cx="4.5" cy="4" r="1.2" fill="#fff"/></svg>PO Box 2481, Rivermead, NSW 2300</li>
        <li><svg width="9" height="9" viewBox="0 0 9 9"><path d="M2 0.5l1.5 2-1 1c.6 1.3 1.6 2.3 3 3l1-1 2 1.5-1 1.5C4 8.5.5 5 .5 1.5z" fill="#1672b0"/></svg>0400 123 456</li>
        <li><svg width="9" height="9" viewBox="0 0 9 9"><rect x="1" y="1" width="7" height="7" fill="#1672b0"/></svg>Business Address</li>
        <li><svg width="9" height="9" viewBox="0 0 9 9"><rect x="1" y="1" width="7" height="7" fill="#1672b0"/></svg>Suite 2.05, 9 Bay Avenue, Rivermead NSW 2300</li>
        <li><svg width="9" height="9" viewBox="0 0 9 9"><rect x="0.5" y="2" width="8" height="5.5" fill="#1672b0"/><path d="M0.5 2l4 3 4-3" stroke="#fff" stroke-width=".8" fill="none"/></svg>hello@plumvessel.net</li>
      </ul>
    </div>
    <div class="col-social">
      <h5>Follow Us</h5>
      <ul>
        <li><span></span>Friendwall</li>
        <li><span></span>Chirpline</li>
        <li><span></span>Pinboardly</li>
        <li><span></span>Snapframe</li>
      </ul>
    </div>
  </div>
</footer>
<div class="copyright">Copyright © 2017 - All Rights Reserved</div>

</body>
</html>
```